Mobile Repair Service on location needs a Web Design

We are starting a new mobile device repair service called Handset Haven and our website needs a design!

Hello Designers!
First, we'd like to make clear this is more than a simple web design contest, we want the designers to create an idea. We want someone who can create the whole theme of the service's we provide. We want someone that can help design our visual branding, help us communicate a sentiment. And we are willing to pay for that.

Who are we?
Our company is based in Rotterdam, the Netherlands. We provide different services for all kinds of electronic devices. The kind of services we provide are, among other things, installations of hardware and software and the repair of broken or malfunctioning devices.
We are starting a new service that offers mobile device repairs on location, be it at the home of our customers, their office, or any other place. Just give us the address and we will come to you for the repair job. This is also our main USP. We have multiple skilled engineers who drive trough the country on a daily basis and can be on location within a working day. Repair is done immediately onsite while the customer waits. At this stage we will start with the smartphone product-group within the mobile devices. In a second phase we might also add tablets.
People don't want to be without their phone for weeks because of some parts that needed to be ordered by a repair center they had to sent their phone to. We offer a fully functional mobile repair center in the form of specially customized vans. These vans have all the tools and utilities needed by our engineers to safely repair your mobile device. Your phone is being repaired directly in front of you, the next business-day, on a location you desire.

For this new service we are creating a website called Handset Haven. The website needs a story and matching design and this is where you come in. We are not looking for a simple template design we can get from any place. We need a story. We want you to create an idea, build a unique theme or vision that helps sell the product/service. This goes beyond the design of the website. We need the whole package, the design you are creating needs to have returning elements like icons, color use, images, maybe even characters etc. You name it! There needs to be a common thread in the design so we can reuse elements in, for example, the email templates, the work order or receipt we give to our customers (we may contact the winner of the contest to design these for us as well!).

The name 'Handset Haven' is chosen. Rehab (short for rehabilitate) has a bold and playful tone to it and the design needs to reflect the name. So we're looking for a somewhat playful and cheeky design. Definitely not too serious and definitely modern. We already got a logo that we love and that fit's this description (see attached design documents for the logo). It's bold, powerful and fun. Our web design needs to reflect this as well and has to fit in with our logo.
We would really like it if the design somehow incorporates elements that highlight our unique selling points (repairs on location, we come to you etc.). We would really like some form of story telling in the design. Think clumsy people breaking their phones. Teenagers in tears because they have no access to their friends. People nowadays have the need to always be 'connected'. What happens when your phone is broken or malfunctioning? We're handling tech, we are nerds and a little bit weird, but we're professionals and here to help you with your problem. The sentiment Byte Brigade tries to communicate is something we really like. We're looking for fresh idea's, anything goes!

In an overview all Unique Selling Points of the Handset haven service:
- Professional service on location. Don’t ship to us we will come to you!
- Clear pricing upfront. No hidden cost.
- Next business-day repair.
- Backed by a professional call center open 12 hours a day and open on a Saturday as well
- Backed by a professional repair center with more then 12 years of experience
- Repair is done by certified engineers
- 1 year warranty on the repair

The process:
The main function of our website will be for customers to make a repair request. A customer will visit our website and can make a repair request immediately by going through a 'request-order-flow'. In this flow he or she will need to fill in some forms and can select wich type/model/brand of mobile device he or she has and what parts need to be repaired. After a request is placed we will call the customer back (within an hour) for a short intake and to set a date/time and location. Our engineer will meet the customer at the specified location and will repair the device onsite in one of our mobile repair centers, which is a specialized van equipped with all the tools needed for device restorations.
So in short the steps are:
- Choose your device and repair job
- Place the order
- Get a callback within the hour
- Set date and location
- We will come to you.

Website functionality:
Our website is our main form of communication. So the sentiment we want to communicate needs be reflected in the design. We need a main/front page designed (preferably a long scrolling page design) containing:
1. Customers will be able to request a repair job directly on our website. So there will need to be a prominent button/link at the top of our main page that will bring the customer to this 'request-order-flow'. This is the main flow which needs to be full focus on the front page. All other items are secondary.
2. The general information of who we are and what we do, and why the customer should choose us. Preferably in short bullet-point type keywords/sentences with icons or other visual cues. See our unique selling points to get an idea of the information that will be displayed here.
3. There needs to be a section that will explain the process (see above) of a repair request step-by- step, again in brief short key sentences and with (custom) icons.
4. There needs to be a section that explains to the customer he/she can always contact us if they are not sure what the problem is with their device, and for this reason are not sure what repair request they should order.
5. We want to implement some functionality that display customer ratings or customer reviews. So there needs to be room for some kind of widget of plugin we're going to implement which shows these reviews.
6. A 'For business section' where we will explain all the options we provide for corporate clients.
7. Social media links.
8. There needs to be a menu with buttons that leads to the all sections described in the previous points.

For now, we need a design for our front page. In the second phase, when we have picked our winner, we may ask the winner to design the page(s) for our request workflow as well.

EDIT:
Finally, we have a very specific order in mind for the different segments of our website. We would like you to add some more segments that were not in our original brief as well:

1. Top header with order/request button. (should instantly make clear our main USP, we do repairs on location)
2. Our process
3. Our unique selling points / why choose us
4. The kind of repairs we do (broken screens, broken batteries, water damage, broken camera's, no sound etc.)
5. A 'meet our team' section, where we introduce some of our engineers
6. A 'contact us for any questions' section/
7. Testimonials/user reviews
8. A section where we show key performance indicators
9. 'For businesses' sections
10.'Subscribe for newsletter' field
11. Social media buttons

Industry/Entity Type

It Service

Number of Pages Required

1 page

Font styles to use
Sans Serif

Requirements
Must have
• a main/front page, design only
• custom icons/images for banners, adverts online and in print (high res)
Nice to have
• Storytelling in our design.
• Design that fits with our brand new logo.
• Elements like icons to have a flat design.
• Keep in mind that the website will need to be responsive when designing! (Ideally provide an example of the mobile design as well)
• Create a fun and trustworthy feeling.

```html
<!DOCTYPE html>
<html lang="en">
<head>
<meta charset="utf-8">
<title>Handset Haven – Mobile Repair On Location</title>
<link href="https://fonts.googleapis.com/css2?family=Lato:wght@400;700;900&display=swap" rel="stylesheet">
<style>
:root{
  --orange:#e8602c;
  --orange-dark:#d4501f;
  --orange-text:#e65a25;
  --ink:#222;
  --body:#555;
  --hero:#6497ae;
  --grey-bg:#f1f1f1;
  --footer-bg:#fafafa;
  --bar-bg:#ececec;
  --white:#fff;
}
*{box-sizing:border-box;margin:0;padding:0}
html,body{width:1200px;height:3158px;overflow:hidden}
body{font-family:'Lato',sans-serif;color:var(--ink);background:var(--white);position:relative}
.section{position:relative;width:1200px}
.abs{position:absolute}

/* header */
.site-header{height:105px}
.brand{left:100px;top:24px;display:flex;align-items:center;gap:12px}
.brand-dot{width:50px;height:50px;border-radius:50%;background:var(--orange)}
.brand-name{font-weight:900;font-size:26px;line-height:26px;color:var(--ink);width:110px}
.search{left:410px;top:36px;width:330px;height:44px;border:1px solid #cfcfcf;border-radius:3px;font-size:14px;color:#777;padding:12px 14px}
.search svg{position:absolute;right:12px;top:13px}
.cart{left:760px;top:38px;display:flex;align-items:center;gap:10px;font-size:17px;font-weight:700}
.cart-ico{width:38px;height:38px;border-radius:50%;background:var(--orange);display:flex;align-items:center;justify-content:center}
.btn{background:var(--orange);color:var(--white);font-weight:700;border-radius:3px;display:flex;align-items:center;justify-content:center}
.order-btn{left:940px;top:34px;width:160px;height:42px;font-size:14px}

/* nav */
.main-nav{height:55px;background:var(--orange)}
.nav-item{top:0;height:55px;line-height:55px;color:var(--white);font-size:15px;font-weight:700}
.nav-active{left:100px;width:160px;background:var(--orange-dark);text-align:center}
.nav-right{left:590px;width:510px;height:55px;background:var(--orange-dark);display:flex;justify-content:space-around;align-items:center;color:var(--white);font-size:15px;font-weight:700}

/* hero */
.hero{height:516px;background:var(--hero)}
.hero-art{left:90px;top:80px;width:540px;height:436px;background:linear-gradient(160deg,#f2d2b5 0%,#e8c2a0 60%,#6f8fa0 100%);border-radius:6px 6px 0 0}
.hero-title{right:100px;top:90px;text-align:right;color:var(--white);font-weight:700}
.hero-title .l1{font-size:35px}
.hero-title .l2{font-size:27px;margin-top:12px}
.hero-cta{left:830px;top:240px;width:270px;height:52px;border:2px solid var(--white);color:var(--white);font-size:16px;font-weight:700;display:flex;align-items:center;justify-content:center}
.dots{left:1005px;top:348px;display:flex;gap:6px}
.dots span{width:14px;height:14px;border:2px solid var(--white);border-radius:50%}
.dots span.on{background:var(--white)}

/* who */
.who{height:606px;text-align:center}
.sec-title{font-size:30px;font-weight:700;color:var(--orange-text)}
.who .sec-title{padding-top:58px}
.who .sub{font-size:19px;font-weight:700;margin-top:14px}
.who .intro{width:1000px;margin:26px auto 0;font-size:14.5px;line-height:27px;color:var(--body)}
.features{display:flex;justify-content:center;gap:60px;margin-top:40px}
.feature{width:148px}
.bubble{width:142px;height:158px;margin:0 auto}
.feature h3{font-size:16px;font-weight:400;margin-top:20px}
.feature.active h3{color:var(--orange-text)}
.feature p{font-size:12.5px;color:var(--body);line-height:21px;margin-top:10px;width:190px;margin-left:-21px}

/* how */
.how{height:506px;background:var(--orange);color:var(--white)}
.how .sec-title{color:var(--white);text-align:center;padding-top:52px}
.rule{width:80px;height:2px;background:var(--white);margin:16px auto 0;opacity:.8}
.step-circle{width:132px;height:132px;border-radius:50%;background:var(--white);display:flex;align-items:center;justify-content:center}
.step-label{font-size:16px;font-weight:700;text-align:center;line-height:27px;width:200px}

/* services */
.services{height:497px}
.services .sec-title{position:absolute;left:100px;top:54px;font-size:27px}
.usp{left:100px;display:flex;align-items:flex-start;gap:22px;font-size:15px;color:#333;line-height:26px;width:600px}
.usp svg{flex:none;margin-top:2px}
.next-btn{left:155px;top:378px;width:215px;height:50px;font-size:15px}
.repair-photo{left:760px;top:110px;width:440px;height:280px;background:linear-gradient(135deg,#f0dcd0 0%,#b9c0c8 55%,#e9ecef 100%);border-radius:4px}

/* testimonials */
.testimonials{height:475px;background:var(--grey-bg)}
.testimonials .sec-title{text-align:center;padding-top:58px;font-size:29px}
.t-card{top:215px;width:320px;height:140px;border:2px solid var(--orange);background:var(--white);padding:32px 20px 0;font-size:13px;line-height:24px;color:#333}
.t-card.featured{background:var(--orange);color:var(--white)}
.t-icon{position:absolute;left:145px;top:-16px;width:30px;height:30px;border-radius:50%;background:var(--orange);display:flex;align-items:center;justify-content:center;border:3px solid var(--grey-bg)}
.t-name{top:385px;font-size:15px;font-weight:700;color:var(--orange-text)}
.arrow{top:272px}

/* footer */
.site-footer{height:348px;background:var(--footer-bg);border-top:3px solid var(--orange)}
.footer-map{left:90px;top:20px;width:150px;height:150px;background:radial-gradient(circle,#e9edf0,var(--footer-bg));opacity:.9}
.footer-brand{left:100px;top:120px;display:flex;flex-direction:column;align-items:center;gap:12px;width:120px}
.footer-brand .brand-dot{width:70px;height:70px}
.footer-brand .brand-name{font-size:26px;text-align:center;width:140px}
.col-title{font-size:17px;font-weight:700;color:var(--orange-text)}
.links{list-style:none;margin-top:22px;font-size:14px;line-height:32px;color:#333}
.contact-row{display:flex;gap:16px;margin-top:22px}
.c-ico{width:36px;height:36px;border:2px solid var(--orange);border-radius:50%;display:flex;align-items:center;justify-content:center;flex:none}
.contact-row b{font-size:14px}
.contact-row span{font-size:13px;color:#444;line-height:22px}
.field{border:1px solid #999;background:var(--white);font-size:12px;color:#333;padding:8px 10px}
.send-btn{width:120px;height:38px;font-size:13px}

/* bottom bar */
.bottom-bar{height:50px;background:var(--bar-bg)}
.copy{left:100px;top:16px;font-size:14px;color:#333}
.socials{left:870px;top:7px;display:flex;gap:10px}
.socials span{width:36px;height:36px;border-radius:50%;border:2px solid #333}
</style>
</head>
<body>

<header class="section site-header">
  <div class="abs brand"><span class="brand-dot"></span><span class="brand-name">Handset Haven</span></div>
  <div class="abs search">Search
    <svg width="16" height="16" viewBox="0 0 16 16"><circle cx="6.5" cy="6.5" r="5" fill="none" stroke="#333" stroke-width="2"/><line x1="10.5" y1="10.5" x2="15" y2="15" stroke="#333" stroke-width="2"/></svg>
  </div>
  <div class="abs cart"><span class="cart-ico"><svg width="18" height="18" viewBox="0 0 18 18"><rect x="2" y="6" width="14" height="10" rx="2" fill="none" stroke="#fff" stroke-width="2"/><path d="M6 6V4a3 3 0 0 1 6 0v2" fill="none" stroke="#fff" stroke-width="2"/></svg></span>CART: 0 Items</div>
  <div class="abs btn order-btn">Request Order Flow</div>
</header>

<nav class="section main-nav">
  <div class="abs nav-item nav-active">PRODUCTS</div>
  <div class="abs nav-item" style="left:290px">BRANDS</div>
  <div class="abs nav-item" style="left:415px">DEALS</div>
  <div class="abs nav-right"><span>Weekly Ad</span><span>Deal of the Day</span><span>Gift Cards</span><span>Gift Ideas &amp; Registry</span></div>
</nav>

<section class="section hero">
  <div class="abs hero-art" role="img" aria-label="Illustration of a hand holding a smartphone showing the app, with a cup of coffee on the table"></div>
  <div class="abs hero-title"><div class="l1">PROFESSIONAL SERVICE ON LOCATION</div><div class="l2">DON'T SHIP TO US WE WILL COME TO YOU!</div></div>
  <div class="abs hero-cta">1 YEAR WARRANTY ON REPAIR</div>
  <div class="abs dots"><span class="on"></span><span></span><span></span><span></span><span></span></div>
</section>

<section class="section who">
  <h2 class="sec-title">WHO ARE WE?</h2>
  <p class="sub">Clear pricing upfront. No hidden cost.</p>
  <p class="intro">Our company is based in Rotterdam, the Netherlands. We provide different services for all kinds of electronic devices. The kind of services we provide are, among other things, installations of hardware and software and the repair of broken or malfunctioning devices. We are starting a new service that offers mobile device repairs on location, be it at the home of our customers, their office, or any other place.</p>
  <div class="features">
    <div class="feature">
      <svg class="bubble" viewBox="0 0 142 158"><path d="M71 3a68 68 0 0 1 16 134L71 155 55 137A68 68 0 0 1 71 3z" fill="#fff" stroke="#e8602c" stroke-width="3"/><circle cx="71" cy="58" r="13" fill="#e8602c"/><path d="M56 55h30v-5a15 15 0 0 0-30 0z" fill="#f08a3c"/><path d="M47 98a24 22 0 0 1 48 0z" fill="#e8602c"/></svg>
      <h3>Good Professionals</h3><p>These vans have all the tools and utilities needed.</p>
    </div>
    <div class="feature active">
      <svg class="bubble" viewBox="0 0 142 158"><path d="M71 3a68 68 0 0 1 16 134L71 155 55 137A68 68 0 0 1 71 3z" fill="#e8602c" stroke="#e8602c" stroke-width="3"/><path d="M55 52c0 20 14 34 34 34l5-8-9-6-5 4c-6-3-10-7-13-13l4-5-6-9z" fill="none" stroke="#fff" stroke-width="3" stroke-linejoin="round"/><path d="M75 50a12 12 0 0 1 12 12M75 42a20 20 0 0 1 20 20" fill="none" stroke="#fff" stroke-width="3"/></svg>
      <h3>Repair And Service</h3><p>Your phone is being repaired directly in front of you.</p>
    </div>
    <div class="feature">
      <svg class="bubble" viewBox="0 0 142 158"><path d="M71 3a68 68 0 0 1 16 134L71 155 55 137A68 68 0 0 1 71 3z" fill="#fff" stroke="#e8602c" stroke-width="3"/><rect x="57" y="42" width="28" height="48" rx="4" fill="none" stroke="#e8602c" stroke-width="3"/><line x1="57" y1="80" x2="85" y2="80" stroke="#e8602c" stroke-width="3"/></svg>
      <h3>Cell Phones</h3><p>The next business-day, on a location you.</p>
    </div>
    <div class="feature">
      <svg class="bubble" viewBox="0 0 142 158"><path d="M71 3a68 68 0 0 1 16 134L71 155 55 137A68 68 0 0 1 71 3z" fill="#fff" stroke="#e8602c" stroke-width="3"/><rect x="46" y="48" width="42" height="30" rx="2" fill="none" stroke="#e8602c" stroke-width="3"/><line x1="40" y1="84" x2="94" y2="84" stroke="#e8602c" stroke-width="3"/><rect x="84" y="58" width="16" height="28" rx="2" fill="#fff" stroke="#e8602c" stroke-width="3"/></svg>
      <h3>Computer &amp; Tablets</h3><p>This new service we are creating a website called Handset Haven.</p>
    </div>
    <div class="feature">
      <svg class="bubble" viewBox="0 0 142 158"><path d="M71 3a68 68 0 0 1 16 134L71 155 55 137A68 68 0 0 1 71 3z" fill="#fff" stroke="#e8602c" stroke-width="3"/><rect x="54" y="44" width="32" height="44" rx="3" fill="none" stroke="#e8602c" stroke-width="3"/><line x1="61" y1="60" x2="79" y2="60" stroke="#e8602c" stroke-width="3"/><line x1="61" y1="68" x2="79" y2="68" stroke="#e8602c" stroke-width="3"/><line x1="61" y1="76" x2="73" y2="76" stroke="#e8602c" stroke-width="3"/><circle cx="86" cy="44" r="9" fill="#e8602c"/><path d="M86 39v10M81 44h10" stroke="#fff" stroke-width="2"/></svg>
      <h3>Pricing &amp; Deals</h3><p>We want you to create an idea, build a unique theme.</p>
    </div>
  </div>
</section>

<section class="section how">
  <h2 class="sec-title">HOW IT WORKS</h2>
  <div class="rule"></div>
  <svg class="abs" style="left:0;top:0" width="1200" height="506" fill="none" stroke="#fff" stroke-width="2">
    <path d="M256 284c16 6 24 22 24 36M272 312l8 10 6-12"/>
    <path d="M478 336c8-14 18-22 32-26M500 302l10 8-12 6"/>
    <path d="M716 284c16 6 24 22 24 36M732 312l8 10 6-12"/>
    <path d="M940 336c8-14 18-22 32-26M962 302l10 8-12 6"/>
  </svg>
  <div class="abs step-circle" style="left:89px;top:210px"><svg width="56" height="56" viewBox="0 0 56 56" fill="none" stroke="#e8602c" stroke-width="3"><circle cx="28" cy="28" r="9"/><path d="M28 6v8M28 42v8M6 28h8M42 28h8M12 12l6 6M38 38l6 6M44 12l-6 6M18 38l-6 6"/><circle cx="28" cy="28" r="17"/></svg></div>
  <div class="abs step-label" style="left:55px;top:352px">Choose your device and repair job</div>
  <div class="abs step-label" style="left:305px;top:219px">Place the order</div>
  <div class="abs step-circle" style="left:339px;top:272px"><svg width="44" height="50" viewBox="0 0 44 50" fill="none" stroke="#e8602c" stroke-width="3"><rect x="4" y="6" width="30" height="40" rx="3"/><path d="M11 22h16M11 30h16M11 38h10"/><circle cx="34" cy="8" r="7" fill="#e8602c"/></svg></div>
  <div class="abs step-circle" style="left:569px;top:210px"><svg width="52" height="52" viewBox="0 0 52 52" fill="none" stroke="#e8602c" stroke-width="3" stroke-linejoin="round"><path d="M8 10c0 20 14 34 34 34l5-9-10-7-5 5c-7-3-11-7-14-14l5-5-7-10z"/><path d="M30 8l14 0M44 8v14M30 22l13-13"/></svg></div>
  <div class="abs step-label" style="left:535px;top:352px">Get a callback within the hour</div>
  <div class="abs step-label" style="left:790px;top:192px;width:150px">Set date and location</div>
  <div class="abs step-circle" style="left:799px;top:272px"><svg width="44" height="54" viewBox="0 0 44 54" fill="none" stroke="#e8602c" stroke-width="3"><path d="M22 50C10 36 6 28 6 20a16 16 0 0 1 32 0c0 8-4 16-16 30z"/><circle cx="22" cy="20" r="6"/></svg></div>
  <div class="abs step-circle" style="left:1009px;top:210px"><svg width="50" height="50" viewBox="0 0 50 50" fill="none" stroke="#e8602c" stroke-width="3"><path d="M22 6h20v38H22"/><path d="M6 25h24M22 17l8 8-8 8"/></svg></div>
  <div class="abs step-label" style="left:1005px;top:352px;width:140px">We will come to you</div>
</section>

<section class="section services">
  <h2 class="sec-title">OUR HANDSET HAVEN SERVICES</h2>
  <div class="abs usp" style="top:124px"><svg width="32" height="32" viewBox="0 0 32 32" fill="none" stroke="#e8602c" stroke-width="3"><path d="M4 5c0 13 10 23 23 23l3-6-7-5-3 3c-4-2-7-5-9-9l3-3-4-7z"/></svg><span>Backed by a professional call center open 12 hours a day and open on a Saturday as well.</span></div>
  <div class="abs usp" style="top:194px"><svg width="32" height="32" viewBox="0 0 32 32" fill="none" stroke="#e8602c" stroke-width="3"><circle cx="16" cy="16" r="5"/><circle cx="16" cy="16" r="11" stroke-dasharray="5 3"/></svg><span>Backed by a professional repair center with more then 12 years of experience</span></div>
  <div class="abs usp" style="top:257px"><svg width="32" height="32" viewBox="0 0 32 32"><circle cx="16" cy="11" r="6" fill="#e8602c"/><path d="M6 30a10 10 0 0 1 20 0z" fill="#e8602c"/></svg><span>Repair is done by certified engineers</span></div>
  <div class="abs usp" style="top:320px"><svg width="32" height="32" viewBox="0 0 32 32" fill="none" stroke="#e8602c" stroke-width="3"><circle cx="16" cy="12" r="8"/><path d="M11 19l-3 11 8-4 8 4-3-11"/></svg><span>1 year warranty on the repair</span></div>
  <div class="abs btn next-btn">Next business-day repair</div>
  <div class="abs repair-photo" role="img" aria-label="Photo of hands opening a smartphone with a repair tool"></div>
</section>

<section class="section testimonials">
  <h2 class="sec-title">CLIENT TESTIMONIALS</h2>
  <svg class="abs arrow" style="left:40px" width="20" height="36" viewBox="0 0 20 36" fill="none" stroke="#333" stroke-width="2"><path d="M16 4L4 18l12 14"/></svg>
  <svg class="abs arrow" style="left:1140px" width="20" height="36" viewBox="0 0 20 36" fill="none" stroke="#333" stroke-width="2"><path d="M4 4l12 14L4 32"/></svg>
  <div class="abs t-card" style="left:100px"><span class="t-icon"><svg width="14" height="12" viewBox="0 0 14 12"><path d="M1 1h12v7H6l-3 3V8H1z" fill="#fff"/></svg></span>"Nemo enim ipsam voluptatem quia voluptas sit aspernatur aut odit aut fugit, sed quia con sequuntur magni dolores eos qui ratione vo luptatem sequi nesciunt."</div>
  <div class="abs t-card featured" style="left:440px"><span class="t-icon"><svg width="14" height="12" viewBox="0 0 14 12"><path d="M1 1h12v7H6l-3 3V8H1z" fill="#fff"/></svg></span>"Nemo enim ipsam voluptatem quia voluptas sit aspernatur aut odit aut fugit, sed quia con sequuntur magni dolores eos qui ratione vo luptatem sequi nesciunt."</div>
  <div class="abs t-card" style="left:780px"><span class="t-icon"><svg width="14" height="12" viewBox="0 0 14 12"><path d="M1 1h12v7H6l-3 3V8H1z" fill="#fff"/></svg></span>"Nemo enim ipsam voluptatem quia voluptas sit aspernatur aut odit aut fugit, sed quia con sequuntur magni dolores eos qui ratione vo luptatem sequi nesciunt."</div>
  <div class="abs t-name" style="left:128px">- Halvorsen</div>
  <div class="abs t-name" style="left:468px">- Piet Verhoef</div>
  <div class="abs t-name" style="left:808px">- Lindqvist</div>
</section>

<footer class="section site-footer">
  <div class="abs footer-map" role="img" aria-label="Faint world map background"></div>
  <div class="abs footer-brand"><span class="brand-dot"></span><span class="brand-name">Handset Haven</span></div>

  <div class="abs" style="left:265px;top:44px">
    <h4 class="col-title">ORDERS &amp; RETURNS</h4>
    <ul class="links">
      <li>› Order Status</li><li>› Shipping, Delivery &amp; Store Pickup</li><li>› Return &amp; Exchange Promise</li><li>› Price Match Guarantee</li><li>› Pay With Points</li><li>› More Orders &amp; Returns Help</li>
    </ul>
  </div>

  <div class="abs" style="left:535px;top:44px">
    <h4 class="col-title">CONTACT US</h4>
    <div class="contact-row"><span class="c-ico"><svg width="14" height="18" viewBox="0 0 14 18" fill="none" stroke="#e8602c" stroke-width="2"><path d="M7 17C2 11 1 8 1 6a6 6 0 0 1 12 0c0 2-1 5-6 11z"/><circle cx="7" cy="6" r="2"/></svg></span><div><b>ADDRESS,</b><br><span>48 W. Harbour Lane<br>Dunmore, NL 3011</span></div></div>
    <div class="contact-row" style="margin-top:14px"><span class="c-ico"><svg width="12" height="18" viewBox="0 0 12 18" fill="none" stroke="#e8602c" stroke-width="2"><rect x="1" y="1" width="10" height="16" rx="2"/></svg></span><div><b>PHONE:</b><br><span>180 044 7719</span></div></div>
    <div class="contact-row" style="margin-top:14px"><span class="c-ico"><svg width="18" height="14" viewBox="0 0 18 14" fill="none" stroke="#e8602c" stroke-width="2"><rect x="1" y="1" width="16" height="12"/><path d="M1 1l8 6 8-6"/></svg></span><div><b>Mail:</b><br><span>info@handsethaven.com</span></div></div>
  </div>

  <div class="abs" style="left:815px;top:44px;width:285px">
    <h4 class="col-title">CONTACT FORM</h4>
    <div style="display:flex;gap:10px;margin-top:24px"><div class="field" style="width:137px;height:36px">Name</div><div class="field" style="width:137px;height:36px">Phone</div></div>
    <div class="field" style="width:284px;height:66px;margin-top:8px">Message</div>
    <div class="btn send-btn" style="margin-top:14px">SEND MESSAGE</div>
  </div>
</footer>

<div class="section bottom-bar">
  <div class="abs copy">Copyright © 2017 Handset Haven. All Rights Reserved.</div>
  <div class="abs socials"><span></span><span></span><span></span><span></span><span></span></div>
</div>

</body>
</html>
```